AGP letterhead

We need a letterhead design for our new company based in Los Angeles called "Amber Gate Pictures". We develop film and television projects. We work with investors, financiers, film production companies, film distribution and sales companies as well as studios. We would like to incorporate our logo (see attached) but make the letterhead simple and elegant. We need to include: logo, company address, phone number and company website.
Updates

Hello designers, Thanks for your submissions. For our letterhead, we are looking for something more simple and elegant. No heavy bars or lines. Make it feel light and clean. Not a lot of ink on the page. Use the logo and contact info but think "clean", "streamlined" and mostly white paper. Looking forward to seeing more... thanks! Amber Gate Pictures team

Target Market(s)

Studio executives, talent agents and agencies, financiers, investors.

Industry/Entity Type

It Company

Requirements
Must have
• Amber Gate Pictures logo (see attached). Logo may be cropped and altered appropriately for elegant letterhead design.
• Please include:
• COMPANY ADDRESS:
• Tolvane Arts Park
• 2850 Delmore Street
• Crest Hall, 2nd Floor
• Seacliff Harbor, CA 90499
• COMPANY WEBSITE:
• www.ambergatepicturesco.example
• COMPANY PHONE NUMBER:
• 555-604-2187

```html
<!DOCTYPE html>
<html lang="en">
<head>
<meta charset="utf-8">
<title>Amber Gate Pictures — Letterhead</title>
<link rel="stylesheet" href="https://fonts.googleapis.com/css2?family=Source+Sans+3:wght@400;600&display=swap">
<style>
  :root {
    --paper: #ffffff;
    --ink: #2b2b2b;
    --mark-ground: #000000;
    --accent: #3fc6f0;
    --accent-soft: #8fdcf5;
  }
  html, body {
    margin: 0;
    padding: 0;
    overflow: hidden;
    background: var(--paper);
  }
  .letterhead {
    position: relative;
    width: 927px;
    height: 1200px;
    background: var(--paper);
    overflow: hidden;
    font-family: "Source Sans 3", "Myriad Pro", sans-serif;
    color: var(--ink);
  }
  .brand-block {
    position: absolute;
    left: 108px;
    top: 0;
    width: 161px;
    height: 178px;
    background: var(--mark-ground);
    display: flex;
    flex-direction: column;
    align-items: center;
    justify-content: center;
    gap: 18px;
  }
  .brand-dot {
    width: 56px;
    height: 56px;
    border-radius: 50%;
    background: var(--accent);
  }
  .brand-name {
    margin: 0;
    font-size: 13px;
    font-weight: 600;
    letter-spacing: 1.5px;
    line-height: 1.25;
    text-align: center;
    text-transform: uppercase;
    color: var(--accent);
  }
  .contact {
    position: absolute;
    right: 139px;
    top: 1121px;
    font-size: 12.5px;
    line-height: 1;
    text-align: right;
  }
  .contact-row {
    display: flex;
    align-items: center;
    justify-content: flex-end;
  }
  .address {
    margin: 0;
    white-space: nowrap;
  }
  .divider {
    width: 3px;
    height: 30px;
    background: var(--accent-soft);
    margin: 0 18px 0 18px;
  }
  .phone {
    margin: 0;
    white-space: nowrap;
  }
  .phone-label {
    font-weight: 600;
    margin-right: 6px;
  }
  .website {
    margin: 8px 0 0;
    font-size: 13.5px;
  }
</style>
</head>
<body>
  <main class="letterhead">
    <header class="brand-block">
      <span class="brand-dot" aria-hidden="true"></span>
      <p class="brand-name">Amber Gate<br>Pictures</p>
    </header>

    <footer class="contact">
      <div class="contact-row">
        <p class="address">Tolvane Arts Park 2850 Delmore Street Crest Hall, 2nd Floor Seacliff Harbor, CA 90499</p>
        <span class="divider" aria-hidden="true"></span>
        <p class="phone"><span class="phone-label">P :</span>555-604-2187</p>
      </div>
      <p class="website">www.ambergatepicturesco.example</p>
    </footer>
  </main>
</body>
</html>
```